RW Holloway LLC Business Card - Civil Engineering & Consulting Firm

We need a Business Card that is elegant, and masculine.  It is our Professional Civil Engineering & Consulting Company located in San Antonio TX (Not s construction or builder firm- no gears & no tool images please). We provide civil engineering services including  commercial site plans, grading and drainage plans, utility plans, hydraulics and hydrology, land planning, utility coordination, and other general civil engineering services related to commercial and residential development.
We have 2 existing Logos. We would like to convey reliability, strength, trustworthiness and attention to detail.  Blues and orange tones as per logo We are OK with the use of a darker blue in the mix.  We have 2 logo versions - Full Company Name Logo to go on the back of card, & Small Icon Logo for the front w/ personal Info.

Target Market(s)
Architects, Real Estate Developers, Other Strctural Engineers, Surveyers, General Contractors
Industry/Entity Type
Professional Civil Engineering
Contact Information for Business Card
Name, Position, Address, Cell & Office #, email, and company website
Font styles to use
Other font styles liked:
- Avian
Requirements
Should not have
- No Tools, No Gears, no Cranes, or Construction Equipment.

```html
<!DOCTYPE html>
<html lang="en">
<head>
<meta charset="utf-8">
<title>RW Holloway LLC – Business Card</title>
<link rel="stylesheet" href="https://fonts.googleapis.com/css2?family=Arimo:wght@400&family=Jost:wght@400&display=swap">
<style>
  :root {
    --page-bg: #e8e5e2;
    --card-blue: #7aaed8;
    --card-orange: #f0922b;
    --text-light: #ffffff;
    --seal-light: #f6f4f3;
    --seal-mid: #e4dcdb;
    --seal-edge: #cfc7c6;
    --brand-blue: #6fa3d3;
  }
  html, body {
    margin: 0;
    padding: 0;
    width: 1200px;
    height: 900px;
    overflow: hidden;
    background: var(--page-bg);
  }
  .canvas {
    position: relative;
    width: 1200px;
    height: 900px;
  }
  .business-card {
    position: absolute;
    left: 100px;
    top: 140px;
    width: 1000px;
    height: 620px;
    overflow: hidden;
    background: var(--card-blue);
    box-shadow: 0 10px 30px rgba(0,0,0,0.12);
  }
  .accent-panel {
    position: absolute;
    left: 678px;
    top: 0;
    width: 322px;
    height: 100%;
    background: var(--card-orange);
  }
  .brand-seal {
    position: absolute;
    left: 412px;
    top: 44px;
    width: 532px;
    height: 532px;
    border-radius: 50%;
    background: radial-gradient(circle at 45% 40%, var(--seal-light) 0%, var(--seal-mid) 65%, var(--seal-edge) 100%);
    display: flex;
    align-items: center;
    justify-content: center;
    gap: 14px;
  }
  .brand-mark {
    width: 22px;
    height: 22px;
    background: var(--card-orange);
  }
  .brand-name {
    font-family: "Arimo", Arial, sans-serif;
    font-weight: 400;
    font-size: 40px;
    letter-spacing: 1px;
    color: var(--brand-blue);
  }
  .person {
    position: absolute;
    left: 59px;
    top: 74px;
    color: var(--text-light);
  }
  .person-name {
    margin: 0;
    font-family: "Jost", "Century Gothic", sans-serif;
    font-weight: 400;
    font-size: 38px;
    line-height: 1;
    letter-spacing: 0.5px;
  }
  .person-title {
    margin: 6px 0 0;
    font-family: "Arimo", Arial, sans-serif;
    font-size: 25px;
    line-height: 1;
  }
  .contact-list {
    position: absolute;
    left: 59px;
    top: 338px;
    margin: 0;
    padding: 0;
    list-style: none;
    font-family: "Arimo", Arial, sans-serif;
    font-size: 27px;
    color: var(--text-light);
  }
  .contact-item {
    display: flex;
    align-items: center;
    gap: 9px;
    height: 36px;
  }
  .contact-icon {
    width: 26px;
    height: 26px;
    flex: none;
  }
  .address {
    position: absolute;
    left: 60px;
    top: 472px;
    margin: 0;
    font-family: "Arimo", Arial, sans-serif;
    font-style: normal;
    font-size: 27px;
    line-height: 36px;
    color: var(--text-light);
  }
</style>
</head>
<body>
<main class="canvas">
  <section class="business-card">
    <div class="accent-panel"></div>

    <div class="brand-seal">
      <span class="brand-mark"></span>
      <span class="brand-name">RW Holloway LLC</span>
    </div>

    <header class="person">
      <h1 class="person-name">DANIEL MERCER</h1>
      <p class="person-title">MANAGING DIRECTOR</p>
    </header>

    <ul class="contact-list">
      <li class="contact-item">
        <svg class="contact-icon" viewBox="0 0 24 24" aria-hidden="true">
          <path d="M6.6 3.5l2.6 3.3-1.6 2.2c1.1 2.4 3 4.3 5.4 5.4l2.2-1.6 3.3 2.6-1.6 3.1c-7.2-.4-12.6-5.8-13-13z" fill="none" stroke="#fff" stroke-width="1.8" stroke-linejoin="round"/>
          <path d="M14 3.5a6.5 6.5 0 0 1 6.5 6.5M14 7a3 3 0 0 1 3 3" fill="none" stroke="#fff" stroke-width="1.6" stroke-linecap="round"/>
        </svg>
        <span>210-555 018 442</span>
      </li>
      <li class="contact-item">
        <svg class="contact-icon" viewBox="0 0 24 24" aria-hidden="true">
          <rect x="2" y="6" width="20" height="13" fill="#fff"/>
          <path d="M2 6l10 7 10-7M2 19l7.5-6.5M22 19l-7.5-6.5" fill="none" stroke="var(--card-blue)" stroke-width="1.4"/>
        </svg>
        <span>info@rwholloway.example</span>
      </li>
      <li class="contact-item">
        <svg class="contact-icon" viewBox="0 0 24 24" aria-hidden="true">
          <g fill="none" stroke="#fff" stroke-width="1.5">
            <circle cx="12" cy="12" r="9.5"/>
            <ellipse cx="12" cy="12" rx="4.5" ry="9.5"/>
            <path d="M2.5 12h19M4 7h16M4 17h16M12 2.5v19"/>
          </g>
        </svg>
        <span>www.rwholloway.example</span>
      </li>
    </ul>

    <address class="address">Address line goes here<br>78205, San Antonio TX</address>
  </section>
</main>
</body>
</html>
```